Quorvix banner ad for roofing company

We need an ad created for a Quorvix banner advertising campaign for a UK based roofing company.

The design should have a large photograph on the background (see attached).
The design should have our Glimmerdew rating (5 stars).
There should be a large text header at the top which reads "Your local roofing experts"

The following services should be listed:
- New roofs
- General roof repairs
- Drone surveys
- Single ply roofing
- Steel cladding
- Asbestos removal

The company logo needs to be visible (attached). Also the company telephone number 020 7946 0321 and website www.brinthoveroofing.com

The advert needs to be horizontal/landscape design. For full spec, please see here: https://promo.quorvix.com/advertiser-help/guides/ad-formats/single-photo-ads

Size required: 1.91:1 - 1200 x 628 pixels

```html
<!DOCTYPE html>
<html lang="en">
<head>
<meta charset="utf-8">
<title>Brinthove Roofing – banner ad</title>
<link rel="stylesheet" href="https://fonts.googleapis.com/css2?family=Montserrat:wght@400;500;700;800&display=swap">
<style>
  :root {
    --canvas: #ffffff;
    --blue-light: #1e92c2;
    --blue-deep: #0b4f86;
    --blue-band: #0a3f86;
    --blue-band-edge: #1560a8;
    --cyan-head: #a9e3f2;
    --white: #ffffff;
    --rule: #2fa6d6;
    --green-badge: #00b67a;
    --photo-green: #5d7f45;
    --photo-grey: #a9aca4;
  }
  * { margin: 0; padding: 0; box-sizing: border-box; }
  html, body {
    width: 1200px; height: 1200px; overflow: hidden;
    background: var(--canvas);
    font-family: "Montserrat", sans-serif;
  }
  .banner {
    position: absolute; left: 125px; top: 361px;
    width: 950px; height: 497px; overflow: hidden;
    background: linear-gradient(170deg, var(--blue-light) 0%, #1677ad 50%, var(--blue-deep) 100%);
    color: var(--white);
  }
  .banner-art { position: absolute; inset: 0; }
  .brand {
    position: absolute; left: 0; width: 360px; top: 20px;
    text-align: center;
  }
  .brand-dot {
    display: block; width: 31px; height: 31px; margin: 0 auto 8px;
    border-radius: 50%; background: var(--white);
  }
  .brand-name {
    font-size: 25px; font-weight: 700; letter-spacing: -0.5px;
    color: var(--white);
  }
  .headline {
    position: absolute; left: 0; width: 360px; top: 128px;
    text-align: center; font-weight: 800; font-size: 40px;
    line-height: 40px; letter-spacing: -0.5px; color: var(--cyan-head);
  }
  .rule {
    position: absolute; left: 27px; width: 305px; height: 1px;
    background: linear-gradient(90deg, transparent, var(--rule), transparent);
  }
  .rule-top { top: 247px; }
  .rule-bottom { top: 356px; }
  .services {
    position: absolute; top: 266px; list-style: none;
    font-size: 15px; font-weight: 400; line-height: 21.5px;
  }
  .services li::before { content: "• "; font-size: 11px; vertical-align: 2px; }
  .services-left { left: 27px; }
  .services-right { left: 195px; }
  .contact {
    position: absolute; left: 0; width: 360px; top: 372px;
    text-align: center; font-weight: 500; font-size: 22px;
    line-height: 26px; letter-spacing: 0.5px;
  }
  .rating {
    position: absolute; left: 27px; top: 458px;
    display: flex; align-items: center; font-size: 10.5px; letter-spacing: 0.5px;
  }
  .rating-stars { display: flex; gap: 1.5px; margin: 0 9px 0 9px; }
  .rating-stars span { width: 19px; height: 19px; background: var(--green-badge); }
  .rating-site { margin-left: 10px; font-size: 13px; font-weight: 500; letter-spacing: 0; }
</style>
</head>
<body>
  <section class="banner">
    <svg class="banner-art" width="950" height="497" viewBox="0 0 950 497">
      <defs>
        <linearGradient id="photo-tone" x1="0" y1="0" x2="1" y2="1">
          <stop offset="0" stop-color="#6d8b4f"/>
          <stop offset="0.45" stop-color="#a9aca4"/>
          <stop offset="1" stop-color="#5d7f45"/>
        </linearGradient>
      </defs>
      <path d="M430 0 Q340 248 430 497 L470 497 Q375 248 470 0 Z" fill="var(--blue-band-edge)"/>
      <path d="M445 0 Q355 248 445 497 L475 497 Q385 248 475 0 Z" fill="var(--blue-band)"/>
      <path d="M469 0 Q380 248 469 497 L950 497 L950 0 Z" fill="url(#photo-tone)"
            role="img" aria-label="Aerial drone photograph of a residential campus with flat-roofed apartment blocks, paths and green lawns"/>
    </svg>

    <div class="brand">
      <span class="brand-dot"></span>
      <span class="brand-name">brinthoveroofing</span>
    </div>

    <h1 class="headline">Your local<br>roofing experts</h1>

    <div class="rule rule-top"></div>
    <ul class="services services-left">
      <li>New roofs</li>
      <li>General roof repairs</li>
      <li>Drone surveys</li>
    </ul>
    <ul class="services services-right">
      <li>Single ply roofing</li>
      <li>Steel cladding</li>
      <li>Asbestos removal</li>
    </ul>
    <div class="rule rule-bottom"></div>

    <p class="contact">020 7946 0321<br>www.brinthoveroofing.com</p>

    <div class="rating">
      <span>Rated “Excellent”</span>
      <span class="rating-stars" role="img" aria-label="Five star rating"><span></span><span></span><span></span><span></span><span></span></span>
      <span>on</span>
      <span class="rating-site">Glimmerdew</span>
    </div>
  </section>
</body>
</html>
```